Black Granite Web Design Project

We are looking for a design for a new company that will be selling Black Granite slabs and tiles. We will be selling to both end-consumers and granite installers. We have already settled on a logo and hopefully this will give an idea of what we like in our designs. We are not going to be selling online but want people to call us so the site is basically an enhanced business card. We will be focusing a lot on SEO so the design will have to keep that in mind.

We would like to keep the design in 1024x768 to make it easily view-able on all devices.

Regarding navigation there should only be a few sub-pages, like "Granite Slabs", "Granite Tiles", "Delivery", "Contact"

Aside from that we are open to designs. One idea we did have was to personalize the site and have a person there somehow to represent the company, making the user feel there are real people behind this site. This is just an idea and not a must.

The name of the company and site is "Copper Ridge Marmora"

Thanks
Updates

Hello All,

Thanks for the great designs. There are some good looking designs that show beautiful kitchens but this site is made for the granite installers and not the retail consumers. So in order not to to confuse the buyers I would like to keep this as much about the raw products as possible. The raw products being the granite slabs, thereby making it obvious we don't sell granite counter tops. 

This design will really be the identity of this company so it is important we get the right message across on this index page and that this page is as complete as possible.

Again, thanks for all the work being put into this.

Target Market(s)

The target audience is granite installers or companies that would with granite slabs.

Industry/Entity Type

Business

```html
<!DOCTYPE html>
<html lang="en">
<head>
<meta charset="utf-8">
<title>Copper Ridge Marmora – Granite Slabs and Tiles</title>
<link rel="stylesheet" href="https://fonts.googleapis.com/css2?family=Open+Sans:wght@400;600;700&family=Arimo:wght@400;700&display=swap">
<style>
  :root {
    --page-bg: #ebebeb;
    --bar-dark: #3b3b3b;
    --panel-dark: #454545;
    --panel-mid: #666666;
    --footer-bg: #444444;
    --footer-base: #1f1f1f;
    --text-light: #ffffff;
    --text-muted: #cfcfcf;
    --text-dark: #222222;
    --rule: #5a5a5a;
  }
  * { box-sizing: border-box; margin: 0; padding: 0; }
  html, body { width: 800px; height: 1200px; overflow: hidden; }
  body {
    position: relative;
    background: var(--page-bg);
    font-family: "Arimo", Arial, sans-serif;
    color: var(--text-dark);
  }
  .abs { position: absolute; }

  /* top bar */
  .topbar { left: 0; top: 0; width: 800px; height: 24px; background: var(--bar-dark); color: var(--text-light); font-size: 9.5px; }
  .topbar .contact { left: 74px; top: 7px; }
  .social { display: flex; gap: 6px; }
  .social span { width: 11px; height: 11px; border-radius: 50%; background: #8a8a8a; display: block; }
  .topbar .social { left: 672px; top: 6px; }

  /* header */
  .brand { left: 74px; top: 50px; display: flex; align-items: center; gap: 8px; }
  .brand .mark { width: 30px; height: 30px; background: #2d2d2d; }
  .brand .name { font-family: "Open Sans", sans-serif; font-weight: 700; font-size: 17px; color: #1e1e1e; }
  .main-nav { left: 355px; top: 47px; width: 376px; height: 30px; background: #2b2b2b; display: flex; border: 1px solid #111; }
  .main-nav a { flex: auto; color: var(--text-light); font-family: "Arimo", sans-serif; font-weight: 700; font-size: 9px; text-decoration: none; text-align: center; line-height: 28px; border-right: 1px solid #4a4a4a; }
  .main-nav a:last-child { border-right: 0; }

  /* hero */
  .hero { left: 74px; top: 105px; width: 651px; height: 262px; background: #3e3e3e; padding: 6px; }
  .hero-photo { width: 100%; height: 100%; position: relative; background: linear-gradient(180deg, #a9b7c2 0%, #8c8873 22%, #8e8066 35%, #c9c4bb 60%, #a8a49d 100%); }
  .hero .arrow { top: 112px; width: 15px; height: 15px; border-radius: 50%; background: #222; }
  .hero .arrow.prev { left: 10px; } .hero .arrow.next { right: 10px; }
  .hero .arrow svg { display: block; }
  .hero-title { left: 5px; top: 143px; width: 340px; padding: 6px 12px; background: rgba(255,255,255,.82); font-family: "Open Sans", sans-serif; font-weight: 600; font-size: 16px; line-height: 22px; color: #222; }
  .hero-bubble { left: 425px; top: 44px; width: 178px; padding: 6px 8px; background: rgba(255,255,255,.72); border-radius: 4px; font-size: 8.5px; line-height: 12px; color: #222; }
  .hero-bubble .who { text-align: right; font-weight: 700; font-size: 8px; margin-top: 3px; }

  /* welcome */
  .welcome { left: 74px; top: 375px; width: 651px; height: 70px; background: var(--panel-dark); color: var(--text-light); padding: 9px 13px; }
  .welcome h1 { font-family: "Open Sans", sans-serif; font-weight: 400; font-size: 13px; margin-bottom: 6px; }
  .welcome p { font-size: 8px; line-height: 12px; width: 510px; text-transform: uppercase; }
  .welcome .seal { right: 16px; top: 5px; width: 60px; height: 60px; border-radius: 50%; background: #2a2a2a; border: 3px solid #ddd; }

  /* features */
  .feature { top: 459px; width: 200px; height: 121px; background: var(--panel-dark); color: var(--text-light); text-align: center; padding-top: 14px; }
  .feature h2 { font-family: "Open Sans", sans-serif; font-weight: 400; font-size: 11px; }
  .feature svg { display: block; margin: 9px auto 8px; }
  .feature p { font-size: 8px; line-height: 10px; }
  .feature .more { font-weight: 700; display: block; }

  /* section bars */
  .section-bar { left: 74px; width: 651px; height: 23px; background: var(--bar-dark); color: var(--text-light); text-align: center; font-family: "Open Sans", sans-serif; font-weight: 600; font-size: 9px; line-height: 23px; }
  .section-bar::after { content: ""; position: absolute; left: 319px; top: 23px; border: 6px solid transparent; border-top: 7px solid var(--bar-dark); }

  /* products */
  .product { top: 632px; width: 197px; }
  .product .swatch { height: 134px; }
  .product .caption { height: 67px; background: var(--panel-mid); color: var(--text-light); text-align: center; padding-top: 8px; }
  .product h3 { font-family: "Arimo", sans-serif; font-weight: 700; font-size: 10px; margin-bottom: 9px; }
  .product p { font-size: 8px; line-height: 10px; }
  .product .more { font-weight: 700; display: block; }
  .mosaic { display: grid; grid-template-columns: repeat(3, 1fr); grid-template-rows: 1fr 1fr; }

  /* tiles carousel */
  .carousel-nav { top: 876px; left: 697px; display: flex; gap: 2px; }
  .carousel-nav span { width: 13px; height: 13px; background: #333; display: block; }
  .tile { top: 892px; width: 114px; height: 112px; }

  /* footer */
  .footer { left: 0; top: 1032px; width: 800px; height: 130px; background: var(--footer-bg); color: var(--text-light); }
  .footer h4 { font-family: "Open Sans", sans-serif; font-weight: 700; font-size: 9px; margin-bottom: 8px; }
  .footer ul { list-style: none; }
  .footer li { font-size: 8.5px; width: 90px; padding: 3px 0 3px 2px; border-bottom: 1px solid var(--rule); }
  .footer li:last-child { border-bottom: 0; }
  .footer .nav-col { left: 80px; top: 12px; }
  .footer .support-col { left: 207px; top: 12px; }
  .footer .support-col li { width: 120px; }
  .footer .callus { right: 80px; top: 13px; font-family: "Arimo", sans-serif; font-weight: 700; font-size: 14px; }
  .footer .foot-brand { right: 80px; top: 48px; display: flex; align-items: center; gap: 5px; font-family: "Open Sans", sans-serif; font-weight: 700; font-size: 11px; color: #1e1e1e; }
  .footer .foot-brand .mark { width: 16px; height: 16px; background: #2b2b2b; }
  .footer address { right: 80px; top: 78px; font-style: normal; text-align: right; font-size: 8.5px; line-height: 12px; color: var(--text-muted); }
  .basebar { left: 0; top: 1162px; width: 800px; height: 38px; background: var(--footer-base); color: var(--text-muted); font-size: 8.5px; }
  .basebar .legal { left: 82px; top: 10px; line-height: 10px; }
  .basebar .social { left: 654px; top: 14px; }
</style>
</head>
<body>

<header>
  <div class="abs topbar">
    <div class="abs contact">Email: hello@copperridgemarmora.test &nbsp; | &nbsp; CALL: (555) 408 2291</div>
    <div class="abs social"><span></span><span></span><span></span><span></span></div>
  </div>
  <div class="abs brand"><span class="mark"></span><span class="name">Copper Ridge Marmora</span></div>
  <nav class="abs main-nav">
    <a href="#">HOME</a><a href="#">ABOUT US</a><a href="#">GRANITE TILES</a><a href="#">GRANITE SLABS</a><a href="#">DELIVERY</a><a href="#">CONTACT US</a>
  </nav>
</header>

<main>
  <section class="abs hero">
    <div class="hero-photo" role="img" aria-label="Granite yard with stacked raw slabs, warehouses and mountains, with the company manager standing arms crossed on the right">
      <div class="abs arrow prev"><svg width="15" height="15" viewBox="0 0 15 15"><path d="M9 4 L6 7.5 L9 11" stroke="#fff" stroke-width="1.6" fill="none"/></svg></div>
      <div class="abs arrow next"><svg width="15" height="15" viewBox="0 0 15 15"><path d="M6 4 L9 7.5 L6 11" stroke="#fff" stroke-width="1.6" fill="none"/></svg></div>
      <div class="abs hero-bubble">Hey!, I am the manager at Copper Ridge Marmora. Let me help you with your purchase<div class="who">TOMAS, MANAGER</div></div>
      <h2 class="abs hero-title">PROFESSIONALLY CUT, HIGH QUALITY GRANITE SLABS FOR YOUR DREAM HOMES</h2>
    </div>
  </section>

  <section class="abs welcome">
    <h1>WELCOME TO COPPER RIDGE MARMORA</h1>
    <p>Sed eget justo tortor, ac ullamcorper nisi. Proin eu consectetur dui. Donec nulla erat, tincidunt eget ultricies id, scelerisque a magna. Morbi congue turpis in justo aliquam feugiat. Praesent et massa ac nibh adipiscing.</p>
    <div class="abs seal"></div>
  </section>

  <article class="abs feature" style="left:74px">
    <h2>PREMIUM QUALITY</h2>
    <svg width="26" height="26" viewBox="0 0 26 26"><rect x="3" y="3" width="20" height="20" fill="none" stroke="#fff" stroke-width="2"/><rect x="7" y="7" width="12" height="12" fill="#fff"/><path d="M9 10h8M9 13h8M9 16h8" stroke="#454545" stroke-width="1.2"/></svg>
    <p>Sed eget justo tortor, ac ullamcorper<br>eu consectetur dui. Donec nulla eget ultric<span class="more">Read more..</span></p>
  </article>
  <article class="abs feature" style="left:299px">
    <h2>PERFECTLY CUT</h2>
    <svg width="26" height="26" viewBox="0 0 26 26"><rect x="2" y="13" width="10" height="10" fill="#fff"/><rect x="14" y="3" width="10" height="10" fill="#fff"/><path d="M5 10 V5 H10 M8 3 L10 5 L8 7" stroke="#fff" stroke-width="2" fill="none"/><path d="M21 16 V21 H16 M18 19 L16 21 L18 23" stroke="#fff" stroke-width="2" fill="none"/></svg>
    <p>Sed eget justo tortor, ac ullamcorper<br>eu consectetur dui. Donec nulla eget ultric<span class="more">Read more..</span></p>
  </article>
  <article class="abs feature" style="left:524px">
    <h2>EXCELLENT SERVICE</h2>
    <svg width="26" height="26" viewBox="0 0 26 26"><circle cx="10" cy="8" r="5" fill="#fff"/><path d="M1 24 C1 16 19 16 19 24 Z" fill="#fff"/><path d="M21 10v8M17 14h8" stroke="#fff" stroke-width="2.4"/></svg>
    <p>Sed eget justo tortor, ac ullamcorper<br>eu consectetur dui. Donec nulla eget ultric<span class="more">Read more..</span></p>
  </article>

  <h2 class="abs section-bar" style="top:590px">OUR PRODUCTS</h2>

  <article class="abs product" style="left:74px">
    <div class="swatch" role="img" aria-label="Close-up of pink and grey speckled granite" style="background:radial-gradient(circle at 30% 40%, #c99c86 0%, #8d7a72 45%, #5a5656 100%)"></div>
    <div class="caption"><h3>GRANITE PRE FABS</h3><p>Sed eget justo tortor, ac ullamcorper<br>eu consectetur dui. Donec nulla eget ultric<span class="more">Read more..</span></p></div>
  </article>
  <article class="abs product" style="left:299px">
    <div class="swatch" role="img" aria-label="Raw granite slab with cream and rust-brown veining" style="background:linear-gradient(135deg, #d9c7ab 0%, #b07a4a 40%, #e6d8c2 70%, #a4683d 100%)"></div>
    <div class="caption"><h3>GRANITE RAW SLABS</h3><p>Sed eget justo tortor, ac ullamcorper<br>eu consectetur dui. Donec nulla eget ultric<span class="more">Read more..</span></p></div>
  </article>
  <article class="abs product" style="left:525px">
    <div class="swatch mosaic" role="img" aria-label="Grid of six granite tile samples in gold, brown, pink and blue">
      <span style="background:#c9a06a"></span><span style="background:#7d5a40"></span><span style="background:#8e6a5a"></span>
      <span style="background:#6f8cb5"></span><span style="background:#b98a8a"></span><span style="background:#2f4a78"></span>
    </div>
    <div class="caption"><h3>GRANITE TILES</h3><p>Sed eget justo tortor, ac ullamcorper<br>eu consectetur dui. Donec nulla eget ultric<span class="more">Read more..</span></p></div>
  </article>

  <h2 class="abs section-bar" style="top:849px">GRANITE TILES</h2>
  <div class="abs carousel-nav">
    <span><svg width="13" height="13" viewBox="0 0 13 13"><path d="M8 3 L4.5 6.5 L8 10" stroke="#fff" stroke-width="1.4" fill="none"/></svg></span>
    <span><svg width="13" height="13" viewBox="0 0 13 13"><path d="M5 3 L8.5 6.5 L5 10" stroke="#fff" stroke-width="1.4" fill="none"/></svg></span>
  </div>
  <div class="abs tile" role="img" aria-label="Golden orange granite tile" style="left:74px;background:linear-gradient(135deg,#d49a5c,#b67a45)"></div>
  <div class="abs tile" role="img" aria-label="Pink and grey speckled granite tile" style="left:194px;background:linear-gradient(135deg,#c9aaa4,#9d8582)"></div>
  <div class="abs tile" role="img" aria-label="Gold and brown granite tile" style="left:315px;background:linear-gradient(135deg,#cf9e5c,#a97a44)"></div>
  <div class="abs tile" role="img" aria-label="Dark grey granite tile" style="left:433px;background:linear-gradient(135deg,#6b6d72,#4c4e54)"></div>
  <div class="abs tile" role="img" aria-label="Cream and green speckled granite tile" style="left:550px;background:linear-gradient(135deg,#d8dacb,#aeb4a2)"></div>
  <div class="abs tile" role="img" aria-label="Pale pink speckled granite tile" style="left:670px;width:54px;background:linear-gradient(135deg,#e0cfc9,#b8a39e)"></div>
</main>

<footer>
  <div class="abs footer">
    <div class="abs nav-col">
      <h4>NAVIGATION</h4>
      <ul><li>Home</li><li>About Us</li><li>Granite Slabs</li><li>Granite Tiles</li><li>Delivery</li><li>Contact Us</li></ul>
    </div>
    <div class="abs support-col">
      <h4>SUPPORT</h4>
      <ul><li>Speak to customer support</li><li>Get in Touch</li><li>Support</li></ul>
    </div>
    <div class="abs callus">CALL US: (555) 408 2291</div>
    <div class="abs foot-brand"><span class="mark"></span><span>Copper Ridge Marmora</span></div>
    <address class="abs">#14, Quarry Lane, Stone Park<br>US 50871<br>PH: 408 229 100</address>
  </div>
  <div class="abs basebar">
    <div class="abs legal">COPYRIGHT 2013. ALL RIGHTS RESERVED.<br>TERMS &amp; CONDITIONS &nbsp;- &nbsp;PRIVACY &nbsp;- &nbsp;DISCLAIMER</div>
    <div class="abs social"><span></span><span></span><span></span><span></span></div>
  </div>
</footer>

</body>
</html>
```